Business Card design for law firm = Brightvale Australia

We are seeking a new design for our business cards.
We are keeping our logo, which is attached.
We need space for
Name
Title
Address is , which is
Level 7
214 Marlowe Street
Sydney NSW 2047
Phone :
Mobile :
Fax :
Email :
DX :
website www.brightvale-example.com.au

Industry/Entity Type

Law Firm / Banking and Finance

Contact Information for Business Card

We are seeking a new design for our business cards. We are keeping our logo. We need space for Name Title Address is Level 7 214 Marlowe Street Sydney NSW 2047 Phone Mobile Fax Email DX website www.brightvale-example.com.au

Colors
0054AA
0677BA
7BADD7
CADEEF
E8F1F8

Requirements
Must have
• see our website for general feel www.brightvale-example.com.au

```html
<!DOCTYPE html>
<html lang="en">
<head>
<meta charset="utf-8">
<title>Brightvale Australia – Business Card</title>
<link rel="stylesheet" href="https://fonts.googleapis.com/css2?family=Quicksand:wght@500;700&display=swap">
<style>
  :root {
    --stage: #1e2124;
    --card-white: #ffffff;
    --brand-blue: #2160ad;
    --brand-light: #1c8fd1;
    --rule-light: #7badd7;
    --ink: #2160ad;
  }
  * { box-sizing: border-box; margin: 0; padding: 0; }
  html, body { width: 1200px; height: 1000px; overflow: hidden; }
  body {
    background: var(--stage);
    font-family: "Quicksand", sans-serif;
    position: relative;
  }
  .card {
    position: absolute;
    width: 530px;
    height: 324px;
    border-radius: 3px;
    overflow: hidden;
    background: var(--card-white);
    box-shadow: 0 14px 30px rgba(0,0,0,.45);
  }
  .brand-name {
    font-weight: 500;
    color: var(--brand-blue);
    letter-spacing: .5px;
    white-space: nowrap;
    line-height: 1;
  }
  /* Front */
  .card-front { left: 50px; top: 150px; }
  .card-front .brand-name {
    position: absolute;
    left: 0; right: 0; top: 138px;
    text-align: center;
    font-size: 44px;
  }
  /* Back */
  .card-back { left: 620px; top: 520px; }
  .back-band {
    position: absolute; left: 0; top: 0; width: 100%; height: 150px;
    background: var(--brand-blue);
  }
  .back-foot {
    position: absolute; left: 0; bottom: 0; width: 100%; height: 24px;
    background: var(--brand-blue);
  }
  .logo-panel {
    position: absolute; right: 16px; top: 14px;
    width: 170px; height: 120px; background: var(--card-white);
    display: flex; align-items: center; justify-content: center;
  }
  .logo-panel .brand-name { font-size: 24px; }
  .identity { position: absolute; left: 24px; top: 22px; color: #fff; }
  .person-name {
    font-size: 26px; font-weight: 700; color: var(--brand-light); letter-spacing: 1px; line-height: 1;
  }
  .person-title { font-size: 11px; font-weight: 700; letter-spacing: .5px; margin-top: 4px; }
  .identity-rule { width: 150px; height: 1px; background: var(--rule-light); margin: 7px 0 8px; }
  .address { font-size: 14px; font-weight: 500; line-height: 1.5; }
  .contacts {
    position: absolute; left: 24px; top: 168px;
    list-style: none; color: var(--ink); font-size: 13.5px; font-weight: 700;
  }
  .contacts li { display: flex; align-items: center; gap: 10px; height: 25px; }
  .contacts svg { width: 14px; height: 14px; flex: none; fill: var(--ink); }
  .contacts .dx-label { width: 14px; font-size: 12px; }
</style>
</head>
<body>

  <section class="card card-front" aria-label="Business card front">
    <span class="brand-name">Brightvale</span>
  </section>

  <section class="card card-back" aria-label="Business card back">
    <div class="back-band"></div>
    <div class="back-foot"></div>

    <div class="logo-panel">
      <span class="brand-name">Brightvale</span>
    </div>

    <div class="identity">
      <p class="person-name">NAME</p>
      <p class="person-title">MANAGING DIRECTOR</p>
      <div class="identity-rule"></div>
      <p class="address">Level 7, 214 Marlowe Street<br>Sydney NSW 2047</p>
    </div>

    <ul class="contacts">
      <li>
        <svg viewBox="0 0 16 16" aria-hidden="true"><circle cx="8" cy="8" r="8"/><path d="M5.2 4.2l1.4-.3.8 2-1 .8c.5 1.1 1.3 1.9 2.4 2.4l.8-1 2 .8-.3 1.4c-3.2.3-6.4-2.9-6.1-6.1z" fill="#fff"/></svg>
        <span>02 9000 0147</span>
      </li>
      <li>
        <svg viewBox="0 0 16 16" aria-hidden="true"><rect x="4" y="1" width="8" height="5"/><rect x="1" y="6" width="14" height="7" rx="1"/><rect x="4" y="10" width="8" height="5" fill="#fff" stroke="#2160ad"/></svg>
        <span>02 9000 0148</span>
      </li>
      <li>
        <svg viewBox="0 0 16 16" aria-hidden="true"><rect x="1" y="3" width="14" height="10" rx="1"/><path d="M1.5 3.5l6.5 5 6.5-5" fill="none" stroke="#fff" stroke-width="1.2"/></svg>
        <span>enquiries@brightvale-example.com.au</span>
      </li>
      <li>
        <span class="dx-label">DX</span>
        <span>318 Sydney</span>
      </li>
      <li>
        <svg viewBox="0 0 16 16" aria-hidden="true"><circle cx="8" cy="8" r="7"/><g fill="none" stroke="#fff" stroke-width="1"><ellipse cx="8" cy="8" rx="3" ry="7"/><path d="M1 8h14M2.5 4.5h11M2.5 11.5h11"/></g></svg>
        <span>www.brightvale-example.com.au</span>
      </li>
    </ul>
  </section>

</body>
</html>
```